The Harbourlight Dental centre, the Zorvik of dentistry

New concept of running a dental practice by having a walk in practice
WE ARE A HUSBAND AND WIFE TEAM

Really modern and sophisticated, we want it to feel different from the traditional dental practice.
we want it split into different pages:CONTACT US
LOCATION: Information about our location since patients often confuse us with the practice across the road
ABOUT US:
Opening hours - & 7 Days, We offer a weekend service
WALK IN: We offer a walk in service for dental treatments
TREATMENTS we offer

DENTAL ADVICE: Free dentist advise call back- So a dentist will call you back for free to discuss

Target Market(s)

Everyone

Industry/Entity Type

Dental

Coding

Coded - Design and coding required

Number of Pages Required

5+ page

Requirements
Must have
• First page
• * changing pictures
• *opening times
• * our walk in concept I.e. no appointment needed
• *logo
• * links in to clinic tidal (online booking system in Australia)
• * address /phone number/email
• * possible videos
• Second page
• meet the team
• third page
• dental treatments/walk in treatments
• fourth page
• dental advice with vid larko videos
• Fifth page
• contact us/maps/ we get confused with the dental practice across the road
• We would also like a giving back page. In this please include the photo's below of our dental mission in Guatemala, where by we did treatment for patients as part of a charity.
Nice to have
• Changing pictures on the home screen
• videos linked to home page

```html
<!DOCTYPE html>
<html lang="en">
<head>
<meta charset="utf-8">
<title>The Harbourlight Dental Centre – Contact Us</title>
<link href="https://fonts.googleapis.com/css2?family=Open+Sans:wght@300;400;600&display=swap" rel="stylesheet">
<style>
  :root{
    --green:#a6c943;
    --green-dark:#93b435;
    --blue:#12a8e3;
    --blue-dark:#0c95d6;
    --text-muted:#a9a9a9;
    --panel:#ececec;
    --field:#ffffff;
    --field-text:#666;
    --submit:#333333;
    --footer:#393939;
    --footer-text:#d8d8d8;
    --footer-line:#4e4e4e;
  }
  *{margin:0;padding:0;box-sizing:border-box}
  html,body{width:1200px;height:862px;overflow:hidden;background:#fff}
  body{font-family:'Open Sans',Arial,sans-serif;position:relative}
  .topbar{position:absolute;top:0;left:0;width:1200px;height:5px;background:linear-gradient(90deg,var(--green) 0 599px,var(--blue) 599px 100%)}

  .brand{position:absolute;left:132px;top:52px;display:flex;align-items:center;gap:10px}
  .brand-square{width:20px;height:20px;background:var(--green)}
  .brand-name{color:var(--green);font-weight:600;font-size:22px;line-height:26px}

  .header-info{position:absolute;right:134px;top:46px;text-align:right}
  .header-meta{font-size:10.4px;color:#666;display:flex;gap:16px;justify-content:flex-end;align-items:center}
  .header-meta span{display:flex;align-items:center;gap:4px}
  .header-contact{margin-top:7px;font-size:17px;color:var(--blue);display:flex;gap:18px;justify-content:flex-end;align-items:center}
  .header-contact span{display:flex;align-items:center;gap:6px}

  .nav{position:absolute;left:132px;top:126px;width:935px;height:54px;background:linear-gradient(#b3d15a,var(--green-dark))}
  .nav a{color:#fff;text-decoration:none;font-size:12px;text-transform:uppercase;position:absolute;top:0;height:54px;line-height:54px;transform:translateX(-50%);white-space:nowrap}
  .nav .nav-contact{position:absolute;left:784px;top:0;width:151px;height:54px;background:linear-gradient(var(--blue),var(--blue-dark))}
  .nav-rule{position:absolute;left:0;top:180px;width:1200px;height:4px;border-top:1px solid #e6e6e6;background:#f4f4f4}

  .section-title{position:absolute;top:225px;font-size:33px;font-weight:300;color:var(--green)}
  .map{position:absolute;left:132px;top:274px;width:460px;height:248px;background:linear-gradient(135deg,#e2e2e2,#cdcdcd)}

  .contact-list{position:absolute;left:136px;top:542px;list-style:none}
  .contact-list li{display:flex;align-items:center;gap:12px;font-size:16px;font-weight:300;color:var(--text-muted);height:24px;margin-bottom:23px}
  .contact-list svg{width:14px;flex:none}

  .form-panel{position:absolute;left:608px;top:274px;width:459px;height:248px;background:var(--panel)}
  .field,.submit{position:absolute;width:182px;height:36px;font-size:12px;line-height:36px}
  .field{background:var(--field);color:var(--field-text);padding-left:17px}
  .submit{background:var(--submit);color:#fff;text-align:center;text-transform:uppercase}

  .photo{position:absolute;top:546px;width:150px;height:112px}
  .photo-outside{left:607px;background:linear-gradient(180deg,#a9c3e0,#c4c4c4)}
  .photo-surgery{left:762px;background:linear-gradient(180deg,#e6e8e6,#c3d79a)}
  .photo-reception{left:917px;background:linear-gradient(180deg,#e8ebe6,#b9d6a6)}

  .footer{position:absolute;left:0;top:718px;width:1200px;height:144px;background:var(--footer);color:var(--footer-text)}
  .footer-item{position:absolute;top:24px;font-size:11.6px;display:flex;align-items:center;gap:8px}
  .social{position:absolute;top:25px;display:flex;gap:17px;left:968px}
  .social span{width:12px;height:12px;border-radius:50%;background:#8a8a8a}
  .footer-rule{position:absolute;left:133px;top:60px;width:936px;height:1px;background:var(--footer-line)}
  .footer-links{position:absolute;left:134px;top:82px;font-size:10px}
  .footer-links span{margin:0 5px}
  .copyright{position:absolute;left:134px;top:108px;font-size:10px}
  .booking{position:absolute;left:795px;top:92px;display:flex;align-items:center;gap:14px;font-size:10px}
  .booking-mark{display:flex;align-items:center;gap:6px;font-size:21px;color:#bdbdbd}
  .booking-mark i{width:14px;height:14px;background:#bdbdbd;display:block}
</style>
</head>
<body>
  <div class="topbar"></div>

  <div class="brand">
    <div class="brand-square"></div>
    <div class="brand-name">The Harbourlight Dental Centre</div>
  </div>

  <div class="header-info">
    <div class="header-meta">
      <span><svg width="8" height="10" viewBox="0 0 8 10"><path d="M4 0a4 4 0 0 0-4 4c0 3 4 6 4 6s4-3 4-6a4 4 0 0 0-4-4zm0 5.5A1.5 1.5 0 1 1 4 2.5a1.5 1.5 0 0 1 0 3z" fill="#777"/></svg>Unit 7, 18 Seabreeze Parade, Karrawind, WA 6071,</span>
      <span><svg width="10" height="10" viewBox="0 0 10 10"><circle cx="5" cy="5" r="4" fill="none" stroke="#777" stroke-width="1.4"/><path d="M5 2.5V5h2" stroke="#777" stroke-width="1.2" fill="none"/></svg>OPEN 8 AM TO 8PM 7 DAYS A WEEK</span>
    </div>
    <div class="header-contact">
      <span><svg width="13" height="13" viewBox="0 0 16 16"><path d="M3.5 1l2.5 3-1.5 2a9 9 0 0 0 5 5l2-1.5 3 2.5-1.5 2.5C7 14 2 9 1 2.5z" fill="currentColor"/></svg>08 6100 2740</span>
      <span><svg width="17" height="13" viewBox="0 0 17 13"><rect width="17" height="13" rx="1" fill="currentColor"/><path d="M1 1.5l7.5 6 7.5-6" stroke="#fff" stroke-width="1.4" fill="none"/></svg>info@harbourlightdental.com</span>
    </div>
  </div>

  <nav class="nav">
    <div class="nav-contact"></div>
    <a style="left:58px">Home</a>
    <a style="left:191px">Meet the Team</a>
    <a style="left:447px">Dental Treatments/Walk-in Treatments</a>
    <a style="left:701px">Dental Advice</a>
    <a style="left:856px">Contact Us</a>
  </nav>
  <div class="nav-rule"></div>

  <h2 class="section-title" style="left:131px">Contact Info</h2>
  <h2 class="section-title" style="left:607px">Contact Us</h2>

  <div class="map" role="img" aria-label="Greyscale world map showing the clinic location"></div>

  <ul class="contact-list">
    <li><svg viewBox="0 0 10 14" height="14"><path d="M5 0a5 5 0 0 0-5 5c0 4 5 9 5 9s5-5 5-9a5 5 0 0 0-5-5zm0 7a2 2 0 1 1 0-4 2 2 0 0 1 0 4z" fill="#b5b5b5"/></svg>Unit 7, 18 Seabreeze Parade, Karrawind, WA 6071</li>
    <li><svg viewBox="0 0 16 16" height="14"><path d="M3.5 1l2.5 3-1.5 2a9 9 0 0 0 5 5l2-1.5 3 2.5-1.5 2.5C7 14 2 9 1 2.5z" fill="#b5b5b5"/></svg>Call Now: 08 6100 2740</li>
    <li><svg viewBox="0 0 17 13" height="11"><rect width="17" height="13" rx="1" fill="#b5b5b5"/><path d="M1 1.5l7.5 6 7.5-6" stroke="#fff" stroke-width="1.4" fill="none"/></svg>Email:&nbsp; info@harbourlightdental.com</li>
  </ul>

  <div class="form-panel">
    <div class="field" style="left:39px;top:50px">First Name</div>
    <div class="field" style="left:239px;top:50px">Last Name</div>
    <div class="field" style="left:39px;top:106px">Phone</div>
    <div class="field" style="left:239px;top:106px">Email</div>
    <div class="field" style="left:39px;top:162px">City</div>
    <div class="submit" style="left:239px;top:162px">Submit</div>
  </div>

  <div class="photo photo-outside" role="img" aria-label="Photo of the clinic building front"></div>
  <div class="photo photo-surgery" role="img" aria-label="Photo of a treatment room"></div>
  <div class="photo photo-reception" role="img" aria-label="Photo of the reception area"></div>

  <footer class="footer">
    <div class="footer-item" style="left:134px"><svg width="10" height="14" viewBox="0 0 10 14"><path d="M5 0a5 5 0 0 0-5 5c0 4 5 9 5 9s5-5 5-9a5 5 0 0 0-5-5zm0 7a2 2 0 1 1 0-4 2 2 0 0 1 0 4z" fill="#d0d0d0"/></svg>Unit 7, 18 Seabreeze Parade, Karrawind, WA 6071</div>
    <div class="footer-item" style="left:488px"><svg width="12" height="12" viewBox="0 0 16 16"><path d="M3.5 1l2.5 3-1.5 2a9 9 0 0 0 5 5l2-1.5 3 2.5-1.5 2.5C7 14 2 9 1 2.5z" fill="#d0d0d0"/></svg>Call Now: 08 6100 2740</div>
    <div class="footer-item" style="left:677px"><svg width="16" height="12" viewBox="0 0 17 13"><rect width="17" height="13" rx="1" fill="#d0d0d0"/><path d="M1 1.5l7.5 6 7.5-6" stroke="#393939" stroke-width="1.4" fill="none"/></svg>Email:&nbsp; info@harbourlightdental.com</div>
    <div class="social" aria-label="Social links"><span></span><span></span><span></span><span></span></div>
    <div class="footer-rule"></div>
    <div class="footer-links">Home<span>|</span>Meet the Team<span>|</span>Dental Treatments/Walk-in Treatments<span>|</span>Dental Advice<span>|</span>Contact us</div>
    <div class="copyright">Copyright &copy; 2016 The Harbourlight Dental centre.&nbsp;&nbsp; All rights reserved.</div>
    <div class="booking">Appointment Booking<div class="booking-mark"><i></i>clinic tidal</div></div>
  </footer>
</body>
</html>
```